Custom unique Stationary design for Logistics company

We need a custom, unique , elegant and luxurious full stationary design using our new logo, following these guidelines:
1- Business card: double sided, both sides uses the navy blue as the background main color (same as the code of the navy blue used in our logo).
2- envelope and folder: also use the same navy blue as the main background color.
3- book cover( notepad cover) : same thing with the navy blue
4- letterhead: feel free to use the combination of the colors in our logo.
5- rest of the items are up to your creativity

Target Market(s)

corporates and other businesses

Industry/Entity Type

Logistics and heavy machines contractors

Requirements
Must have
• Letterhead, business card, envelope, notepad cover, paper, file
Nice to have
• navy blue to be main background color for business card, envelope, notepad cover

```html
<!DOCTYPE html>
<html lang="en">
<head>
<meta charset="utf-8">
<title>Northvane Freight — Envelope</title>
<link href="https://fonts.googleapis.com/css2?family=Montserrat:wght@500;800&display=swap" rel="stylesheet">
<style>
  :root {
    --navy: #084d6e;
    --orange: #e65c30;
    --paper: #f4f3f3;
    --backdrop: #d3d2d2;
    --ink: #1d1d1d;
    --white: #ffffff;
  }
  * { margin: 0; padding: 0; box-sizing: border-box; }
  html, body {
    width: 1200px;
    height: 1050px;
    overflow: hidden;
    background: var(--backdrop);
    font-family: "Montserrat", sans-serif;
  }
  .envelope {
    position: absolute;
    left: 145px;
    width: 910px;
    height: 390px;
    background: var(--paper);
    overflow: hidden;
  }
  .envelope-back { top: 105px; }
  .envelope-front { top: 555px; }

  .flap {
    position: absolute;
    left: 0; top: 0;
    width: 910px;
    height: 131px;
  }
  .flap-name {
    position: absolute;
    top: 46px;
    left: 0;
    width: 100%;
    text-align: center;
    color: var(--white);
    font-weight: 800;
    font-size: 30px;
    letter-spacing: 1px;
  }

  .brand {
    position: absolute;
    left: 42px;
    top: 70px;
    display: flex;
    align-items: center;
    gap: 12px;
  }
  .brand-mark {
    width: 22px;
    height: 22px;
    background: var(--orange);
  }
  .brand-name {
    color: var(--navy);
    font-weight: 800;
    font-size: 44px;
    letter-spacing: 0.5px;
  }
  .return-address {
    position: absolute;
    left: 41px;
    top: 183px;
    font-style: normal;
    font-weight: 500;
    font-size: 15.5px;
    line-height: 20px;
    color: var(--ink);
  }
  .stripes {
    position: absolute;
    left: 0; top: 0;
    width: 910px;
    height: 390px;
  }
</style>
</head>
<body>
  <section class="envelope envelope-back" aria-label="Envelope back">
    <svg class="flap" viewBox="0 0 910 131" aria-hidden="true">
      <path d="M0 0 H910 L885 90 Q870 130 830 131 H80 Q40 130 25 90 Z" fill="var(--navy)"/>
    </svg>
    <div class="flap-name">Northvane Freight</div>
  </section>

  <section class="envelope envelope-front" aria-label="Envelope front">
    <div class="brand">
      <span class="brand-mark"></span>
      <span class="brand-name">Northvane Freight</span>
    </div>
    <address class="return-address">
      1420 Harbour Line, Suite 310<br>
      Brampton, ON L6T 4K9
    </address>
    <svg class="stripes" viewBox="0 0 910 390" aria-hidden="true">
      <polygon points="0,342 604,346 582,360 0,354" fill="var(--orange)"/>
      <polygon points="0,367 590,371 642,340 910,341 910,390 0,390" fill="var(--navy)"/>
    </svg>
  </section>
</body>
</html>
```